Mindfulness School for Children -- Business Cards

We're looking for business cards for our school directors and owners. We're a mindfulness school for children called little lanterns. Attached are our logos/icons.

```html
<!DOCTYPE html>
<html lang="en">
<head>
<meta charset="utf-8">
<title>little lanterns — Business Card</title>
<link rel="stylesheet" href="https://fonts.googleapis.com/css2?family=Alegreya:wght@400&family=Karla:wght@400&display=swap">
<style>
  :root {
    --page-bg: #d9d4cc;
    --card-dark: #0c0c0c;
    --card-mid: #2b2b2b;
    --brand-teal: #4f9c93;
    --name-blue: #3f8fa9;
    --title-green: #4f9b7b;
    --detail-grey: #a2a2a2;
    --icon-green: #4f9b7b;
    --sheen-light: rgba(225, 230, 235, 0.55);
    --sheen-mid: rgba(180, 175, 168, 0.25);
  }
  * { margin: 0; padding: 0; box-sizing: border-box; }
  html, body {
    width: 1200px; height: 969px; overflow: hidden;
    background: var(--page-bg);
  }
  .canvas { position: relative; width: 1200px; height: 969px; }
  .card {
    position: absolute; left: 60px; top: 178px;
    width: 1080px; height: 614px;
    border-radius: 30px; overflow: hidden;
    background: radial-gradient(ellipse at 20% 95%, var(--card-mid) 0%, var(--card-dark) 60%);
    box-shadow: 0 10px 30px rgba(0,0,0,0.25);
  }
  .card__decor {
    position: absolute; left: 535px; top: 0; width: 545px; height: 614px;
    background: radial-gradient(ellipse at 62% 45%, var(--sheen-light) 0%, var(--sheen-mid) 40%, rgba(0,0,0,0) 72%);
  }
  .brand {
    position: absolute; left: 72px; top: 112px;
    font-family: 'Alegreya', serif; font-weight: 400;
    font-size: 54px; line-height: 1; color: var(--brand-teal);
    letter-spacing: 0.5px;
  }
  .person__name {
    position: absolute; left: 72px; top: 219px;
    font-family: 'Alegreya', serif; font-size: 39px; line-height: 1;
    color: var(--name-blue);
  }
  .person__title {
    position: absolute; left: 73px; top: 263px;
    font-family: 'Karla', sans-serif; font-size: 20px; line-height: 1;
    color: var(--title-green); letter-spacing: 0.8px;
  }
  .contact {
    position: absolute; left: 0; top: 0;
    font-family: 'Karla', sans-serif; font-size: 22px; color: var(--detail-grey);
    letter-spacing: 0.6px;
  }
  .contact__row { position: absolute; left: 107px; white-space: nowrap; line-height: 1; }
  .contact__icon { position: absolute; left: 74px; width: 20px; height: 20px; }
</style>
</head>
<body>
<main class="canvas">
  <section class="card" aria-label="Business card">
    <div class="card__decor" role="img" aria-label="Large brand mark decoration area"></div>

    <div class="brand">littlelanterns</div>

    <div class="person__name">Daniel Hayes</div>
    <div class="person__title">President</div>

    <div class="contact">
      <svg class="contact__icon" style="top:316px" viewBox="0 0 20 20" aria-hidden="true">
        <path d="M10 1a6 6 0 0 0-6 6c0 4.5 6 12 6 12s6-7.5 6-12a6 6 0 0 0-6-6z" fill="var(--icon-green)"/>
        <circle cx="10" cy="7" r="2.3" fill="#151515"/>
      </svg>
      <div class="contact__row" style="top:318px">4120 Willow Bend Road</div>
      <div class="contact__row" style="top:348px">Juneau, Alaska 34512</div>

      <svg class="contact__icon" style="top:394px" viewBox="0 0 20 20" aria-hidden="true">
        <path d="M4 2l3 0 2 4-2 2c1 2 3 4 5 5l2-2 4 2v3c0 1-1 2-2 2C9 18 2 11 2 4c0-1 1-2 2-2z" fill="var(--icon-green)"/>
      </svg>
      <div class="contact__row" style="top:393px">555-014-2273</div>

      <svg class="contact__icon" style="top:424px" viewBox="0 0 20 20" aria-hidden="true">
        <rect x="5" y="1" width="10" height="18" rx="2" fill="none" stroke="var(--icon-green)" stroke-width="2"/>
        <circle cx="10" cy="15.5" r="1" fill="var(--icon-green)"/>
      </svg>
      <div class="contact__row" style="top:424px">555-014-2273</div>

      <svg class="contact__icon" style="top:454px" viewBox="0 0 20 20" aria-hidden="true">
        <rect x="5" y="2" width="10" height="5" fill="var(--icon-green)"/>
        <rect x="1" y="8" width="18" height="9" rx="2" fill="var(--icon-green)"/>
        <rect x="5" y="13" width="10" height="5" fill="#151515"/>
      </svg>
      <div class="contact__row" style="top:454px">555-014-2273</div>

      <svg class="contact__icon" style="top:486px" viewBox="0 0 20 20" aria-hidden="true">
        <rect x="2" y="4" width="16" height="12" fill="var(--icon-green)"/>
        <path d="M2 4l8 7 8-7" fill="none" stroke="#151515" stroke-width="1.5"/>
      </svg>
      <div class="contact__row" style="top:485px">name@littlelanterns.com</div>

      <svg class="contact__icon" style="top:516px" viewBox="0 0 20 20" aria-hidden="true">
        <circle cx="10" cy="10" r="8" fill="var(--icon-green)"/>
        <path d="M6 5c2 1 3 3 2 5s1 3 0 6M13 4c-1 2 1 4 3 5" fill="none" stroke="#151515" stroke-width="1.3"/>
      </svg>
      <div class="contact__row" style="top:515px">littlelanterns.com</div>
    </div>
  </section>
</main>
</body>
</html>
```